jQuery Mobile CSS for web app

Task Outline:
Create jQuery Mobile themeroller compliant CSS and icons for a mobile web app.
Task Description:
Brindle Solutions are in the process of implementing a new, web based version of their Tessel operations platform.
The web based version of Tessel is built on top of the jQuery Mobile platform and we are looking for a designer to create a jQuery Mobile themeroller compliant CSS theme pack that we can plug into our application. The aim is to remove the standard jQuery Mobile look and feel and to introduce the Brindle branding throughout the new web app.
A number of screenshots are shown in the attached design spec (brindle_solutions.pdf) that show what the current (Windows Mobile 6.5) application looks like, alongside the development version of our new web app.
Deliverables:
• jQuery Mobile (v 1.4.2) themeroller compliant CSS which provides theming for all jQuery Mobile UI components.
• Example html showing how to use the CSS theme (especially where additional html/css classes are required).
• New set of status icons (as listed in attachment)
Inspiration:
See our website for current branding: www.brindle-solutions-demo.net

```html
<!DOCTYPE html>
<html lang="en">
<head>
<meta charset="utf-8">
<title>Tessel – Item Search</title>
<link href="https://fonts.googleapis.com/css2?family=Roboto:wght@400;500;700&display=swap" rel="stylesheet">
<style>
:root{
  --bar-top:#3a3a3a;
  --bar-bottom:#151515;
  --body-top:#ececec;
  --body-bottom:#d2d2d2;
  --ink:#1e1e1e;
  --muted:#8a8a8a;
  --seg-dark:#2f2f2f;
  --seg-active:#2aa6c1;
  --red:#d9343a;
  --red-dark:#b4232a;
  --green:#8dc21f;
  --card:#f1f1f1;
  --white:#ffffff;
}
*{box-sizing:border-box;margin:0;padding:0}
html,body{width:928px;height:1200px;overflow:hidden}
body{font-family:"Roboto",Arial,sans-serif;color:var(--ink);position:relative;
  background:linear-gradient(var(--body-top),var(--body-bottom))}
.header{position:absolute;left:0;top:0;width:928px;height:137px;
  background:linear-gradient(var(--bar-top),var(--bar-bottom));}
.launch-pad{position:absolute;left:84px;top:34px;width:377px;height:74px;background:var(--white);
  border-radius:10px;display:flex;align-items:center;gap:28px;padding-left:24px;font-size:37px;color:var(--ink)}
.brand{position:absolute;left:470px;top:34px;font-size:46px;font-weight:700;color:var(--white);line-height:74px}
.search-input{position:absolute;left:105px;top:185px;width:720px;height:97px;background:var(--white);
  border:2px solid #d8d8d8;border-radius:14px;font-size:32px;color:var(--muted);padding-left:30px;line-height:93px}
.segment{position:absolute;top:308px;height:82px;border-radius:6px;color:var(--white);font-size:29px;
  font-weight:500;display:flex;align-items:center;justify-content:center;background:linear-gradient(#444,var(--seg-dark))}
.segment.active{background:var(--seg-active)}
.search-btn{position:absolute;left:585px;top:416px;width:243px;height:82px;border-radius:8px;
  background:linear-gradient(#e4474c,var(--red-dark));color:var(--white);font-size:33px;font-weight:500;
  display:flex;align-items:center;justify-content:center;gap:22px;border:2px solid #9e1d22}
.results-label{position:absolute;left:63px;top:558px;font-size:35px;color:#333}
.result{position:absolute;left:55px;width:812px;height:166px;background:linear-gradient(#f6f6f6,#e6e6e6);
  border-radius:8px;box-shadow:0 2px 4px rgba(0,0,0,.25)}
.result .icon{position:absolute;left:95px;top:25px}
.result .lines{position:absolute;left:227px;top:30px;font-size:34px;line-height:61px}
.result .go{position:absolute;left:701px;top:51px}
.footer{position:absolute;left:0;top:1039px;width:928px;height:161px;
  background:linear-gradient(var(--bar-top),var(--bar-bottom))}
.nav-btn{position:absolute;top:39px}
.nav-btn span{position:absolute;top:0;width:100%;line-height:85px;text-align:center;color:var(--white);font-size:37px;font-weight:500}
.screen-code{position:absolute;right:8px;bottom:6px;font-size:26px;color:#c8c8c8}
</style>
</head>
<body>
<header class="header">
  <div class="launch-pad">
    <svg width="42" height="42" viewBox="0 0 42 42" aria-hidden="true">
      <g fill="#1e1e1e"><rect x="0" y="0" width="11" height="11"/><rect x="15" y="0" width="11" height="11"/><rect x="30" y="0" width="11" height="11"/>
      <rect x="0" y="15" width="11" height="11"/><rect x="15" y="15" width="11" height="11"/><rect x="30" y="15" width="11" height="11"/>
      <rect x="0" y="30" width="11" height="11"/><rect x="15" y="30" width="11" height="11"/><rect x="30" y="30" width="11" height="11"/></g>
    </svg>
    Launch pad
  </div>
  <div class="brand">Tessel</div>
</header>

<div class="search-input">Cable</div>
<div class="segment" style="left:105px;width:235px">Serial Number</div>
<div class="segment" style="left:345px;width:235px">Item Number</div>
<div class="segment active" style="left:585px;width:238px">Description</div>
<div class="search-btn">
  <svg width="46" height="46" viewBox="0 0 46 46" aria-hidden="true">
    <circle cx="18" cy="18" r="13" fill="none" stroke="#fff" stroke-width="5"/>
    <line x1="28" y1="28" x2="42" y2="42" stroke="#fff" stroke-width="7" stroke-linecap="round"/>
  </svg>
  Search
</div>

<div class="results-label">Results</div>

<div class="result" style="top:620px">
  <svg class="icon" width="116" height="116" viewBox="0 0 116 116" aria-hidden="true">
    <circle cx="58" cy="58" r="56" fill="#e8e8e8"/><circle cx="58" cy="58" r="48" fill="var(--green)"/>
    <path d="M58 30 L82 42 L82 72 L58 86 L34 72 L34 42 Z" fill="#fff"/>
    <path d="M34 42 L58 54 L82 42 M58 54 L58 86" fill="none" stroke="var(--green)" stroke-width="4"/>
  </svg>
  <div class="lines">30106<br>RAD64002142 ; L62</div>
  <svg class="go" width="64" height="64" viewBox="0 0 64 64" aria-hidden="true">
    <circle cx="32" cy="32" r="30" fill="#5a5a5a"/><path d="M26 19 L39 32 L26 45" fill="none" stroke="#fff" stroke-width="6" stroke-linecap="round" stroke-linejoin="round"/>
  </svg>
</div>

<div class="result" style="top:799px">
  <svg class="icon" width="116" height="116" viewBox="0 0 116 116" aria-hidden="true">
    <circle cx="58" cy="58" r="56" fill="#e8e8e8"/><circle cx="58" cy="58" r="48" fill="var(--green)"/>
    <path d="M58 30 L82 42 L82 72 L58 86 L34 72 L34 42 Z" fill="#fff"/>
    <path d="M34 42 L58 54 L82 42 M58 54 L58 86" fill="none" stroke="var(--green)" stroke-width="4"/>
  </svg>
  <div class="lines">30106<br>RAD64002142 ; L62</div>
  <svg class="go" width="64" height="64" viewBox="0 0 64 64" aria-hidden="true">
    <circle cx="32" cy="32" r="30" fill="#5a5a5a"/><path d="M26 19 L39 32 L26 45" fill="none" stroke="#fff" stroke-width="6" stroke-linecap="round" stroke-linejoin="round"/>
  </svg>
</div>

<footer class="footer">
  <div class="nav-btn" style="left:45px;width:208px;height:85px">
    <svg width="208" height="85" viewBox="0 0 208 85" aria-hidden="true"><path d="M0 42 L32 0 H202 Q208 0 208 6 V79 Q208 85 202 85 H32 Z" fill="#5c6470"/></svg>
    <span style="padding-left:22px">Back</span>
  </div>
  <svg style="position:absolute;left:430px;top:54px" width="68" height="58" viewBox="0 0 68 58" aria-hidden="true">
    <g fill="#bdbdbd"><rect y="0" width="68" height="14" rx="2"/><rect y="22" width="68" height="14" rx="2"/><rect y="44" width="68" height="14" rx="2"/></g>
  </svg>
  <div class="nav-btn" style="left:667px;width:206px;height:85px">
    <svg width="206" height="85" viewBox="0 0 206 85" aria-hidden="true"><path d="M206 42 L174 0 H6 Q0 0 0 6 V79 Q0 85 6 85 H174 Z" fill="#5c6470"/></svg>
    <span style="padding-right:22px">Next</span>
  </div>
  <div class="screen-code">C6</div>
</footer>
</body>
</html>
```